Automotive eCommerce Business looking for a business card design

Looking for a clean and simple business card design. Our company name is "Brindle Auto" and we are a company specializing in the ecommerce sales of automotive parts, specifically for pick up trucks and large SUVs. Our company colours are red, black, and white.

Feel free to use the logo provided or create a new logo that you seem fit. Looking forward to your creative ideas!

Industry/Entity Type

Automotive

Contact Information for Business Card

We were thinking of a possibly two-sided design featuring just the logo and company name on one side, and personal information on the other side. Single sided designs will be considered as well.

Font styles to use
Serif
Sans Serif
Decorative

Colors
ec1f27
ffffff
000000

Requirements
Must have
• Space for employee's name, title, phone number and email address, along with the company address and website somewhere.

```html
<!DOCTYPE html>
<html lang="en">
<head>
<meta charset="utf-8">
<title>Brindle Auto Business Card</title>
<link href="https://fonts.googleapis.com/css2?family=Cinzel:wght@400;600&family=Roboto:wght@400&family=Roboto+Condensed:wght@700&display=swap" rel="stylesheet">
<style>
  :root {
    --backdrop: #6a4c38;
    --card-dark: #4b5153;
    --card-light: #f1f1f1;
    --brand-red: #a11d22;
    --ink-grey: #4a4e51;
    --white: #ffffff;
  }
  html, body {
    margin: 0;
    padding: 0;
    width: 1200px;
    height: 960px;
    overflow: hidden;
    background: var(--backdrop);
  }
  .canvas {
    position: relative;
    width: 1200px;
    height: 960px;
  }
  .card {
    position: absolute;
    left: 320px;
    width: 600px;
    height: 342px;
    border-radius: 18px;
    overflow: hidden;
    box-shadow: 0 4px 10px rgba(0,0,0,0.35);
  }
  .card-back {
    top: 108px;
    background: var(--card-dark);
  }
  .card-front {
    top: 493px;
    background: var(--card-light);
  }
  .back-wordmark {
    position: absolute;
    left: 0;
    width: 100%;
    top: 146px;
    text-align: center;
    font-family: "Cinzel", serif;
    font-weight: 600;
    font-size: 44px;
    color: var(--white);
  }
  .back-web {
    position: absolute;
    left: 0;
    width: 100%;
    top: 296px;
    text-align: center;
    font-family: "Roboto", sans-serif;
    font-size: 14px;
    letter-spacing: 5px;
    color: var(--white);
  }
  .contact-panel {
    position: absolute;
    left: 0;
    top: 0;
  }
  .contact-list {
    position: absolute;
    right: 40px;
    top: 36px;
    margin: 0;
    padding: 0;
    list-style: none;
    font-family: "Roboto", sans-serif;
    font-size: 14px;
    line-height: 19px;
    color: var(--white);
  }
  .contact-list li {
    display: flex;
    justify-content: flex-end;
    align-items: center;
    gap: 13px;
  }
  .contact-list li.address { margin-bottom: 10px; }
  .contact-list .icon {
    width: 14px;
    height: 14px;
    flex: none;
  }
  .brand-mark {
    position: absolute;
    left: 85px;
    top: 140px;
    width: 126px;
    height: 126px;
    border-radius: 14px;
    background: var(--brand-red);
  }
  .company-name {
    position: absolute;
    left: 42px;
    top: 276px;
    font-family: "Cinzel", serif;
    font-weight: 400;
    font-size: 22px;
    color: var(--ink-grey);
    white-space: nowrap;
  }
  .person-name {
    position: absolute;
    left: 352px;
    width: 200px;
    top: 278px;
    text-align: center;
    font-family: "Roboto Condensed", sans-serif;
    font-weight: 700;
    font-size: 22px;
    color: var(--brand-red);
  }
</style>
</head>
<body>
<div class="canvas">

  <section class="card card-back">
    <div class="back-wordmark">Brindle Auto</div>
    <div class="back-web">www.brindleauto.com</div>
  </section>

  <section class="card card-front">
    <svg class="contact-panel" width="600" height="342" viewBox="0 0 600 342" aria-hidden="true">
      <path d="M308,0 H600 V175 L492,230 Q452,250 412,230 L312,180 Q293,170 293,150 V15 Q293,0 308,0 Z" fill="var(--brand-red)"/>
    </svg>

    <ul class="contact-list">
      <li class="address">
        <span style="text-align:right">1420 Harbor View Road<br>Juneau, Alaska 99801</span>
        <svg class="icon" viewBox="0 0 14 14"><path d="M7,0.5 A4.5,4.5 0 0 1 11.5,5 C11.5,8 7,13.5 7,13.5 C7,13.5 2.5,8 2.5,5 A4.5,4.5 0 0 1 7,0.5 Z M7,3.3 A1.7,1.7 0 1 0 7,6.7 A1.7,1.7 0 1 0 7,3.3 Z" fill="#fff" fill-rule="evenodd"/></svg>
      </li>
      <li>
        <span>555 214 7380</span>
        <svg class="icon" viewBox="0 0 14 14"><path d="M3,1 L5,1 L6,4 L4.5,5.2 C5.3,7 7,8.7 8.8,9.5 L10,8 L13,9 L13,11 C13,12 12,13 11,13 C6,12.5 1.5,8 1,3 C1,2 2,1 3,1 Z" fill="#fff"/></svg>
      </li>
      <li>
        <span>555 309 6142</span>
        <svg class="icon" viewBox="0 0 14 14"><rect x="3.5" y="0.5" width="7" height="13" rx="1.2" fill="none" stroke="#fff" stroke-width="1.4"/><circle cx="7" cy="11.3" r="0.8" fill="#fff"/></svg>
      </li>
      <li>
        <span>555 471 2056</span>
        <svg class="icon" viewBox="0 0 14 14"><rect x="3.5" y="1" width="7" height="4" fill="#fff"/><rect x="0.5" y="5" width="13" height="5.5" rx="1" fill="#fff"/><rect x="3.5" y="9" width="7" height="4" fill="#fff" stroke="var(--brand-red)" stroke-width="0.8"/></svg>
      </li>
      <li>
        <span>info@brindleauto.com</span>
        <svg class="icon" viewBox="0 0 14 14"><rect x="1" y="3" width="12" height="8.5" rx="0.8" fill="#fff"/><path d="M1.5,3.5 L7,8 L12.5,3.5" fill="none" stroke="var(--brand-red)" stroke-width="1"/></svg>
      </li>
      <li>
        <span>www.brindleauto.com</span>
        <svg class="icon" viewBox="0 0 14 14"><circle cx="7" cy="7" r="6" fill="#fff"/><path d="M1.5,7 H12.5 M7,1 C4.5,4 4.5,10 7,13 M7,1 C9.5,4 9.5,10 7,13" fill="none" stroke="var(--brand-red)" stroke-width="0.9"/></svg>
      </li>
    </ul>

    <div class="brand-mark" aria-hidden="true"></div>
    <div class="company-name">Brindle Auto Ltd.</div>
    <div class="person-name">OWEN CARTER</div>
  </section>

</div>
</body>
</html>
```